RV7 - Rapid Vigil Field Operations Suite

I need an introductory website for RV7 which describes the features of the product and the ease of use of the product. The product is focused on Preparing for an incident using Volunteer and Resource management and then responding to an incident with Incident Management, Team Management, Task Management and Communication Management. Once a situation is handled, the application provides complete reporting on each of the above aspects

Target Market(s)

Local Government entities, specifically the emergency department directors or coordinators

Industry/Entity Type

Government Office

Coding

Coded - Design and coding required

Font styles to use
Sans Serif

Requirements
Must have
• Clear layout with modern images. I want to be able to get a clear understanding of the features of the product and the ease of use. I would like to high light how the application helps in Communication Management, Team Management, Task Management and Incident Managements. Also, how the use of application helps to get an immediate snap shot of how well an incident was handled. I want to highlight how the Dashboard provides a quick look at the Incident(s) being managed
Nice to have
• I would like to in the future add videos to the site. At this point don't have any ideas about nice to have features
Should not have
• traditional designs. I am looking for a slick, modern looking website. Clean design is the key.

```html
<!DOCTYPE html>
<html lang="en">
<head>
<meta charset="utf-8">
<title>RV7 - Rapid Vigil Field Operations Suite</title>
<link href="https://fonts.googleapis.com/css2?family=Lato:wght@400;700;900&display=swap" rel="stylesheet">
<style>
:root{
  --blue:#1d5fa8;
  --blue-dark:#134a8a;
  --navy:#0f3a70;
  --green:#8dc63f;
  --green-dark:#76ad2c;
  --ink:#333;
  --muted:#666;
  --white:#fff;
}
*{box-sizing:border-box;margin:0;padding:0}
html,body{width:1200px;height:3103px;overflow:hidden}
body{font-family:'Lato',Arial,sans-serif;color:var(--ink);background:#fff;position:relative}
.abs{position:absolute}
section,header,nav,footer{position:absolute;left:0;width:1200px}

/* header */
.site-header{top:0;height:114px;border-top:4px solid var(--blue)}
.brand{left:100px;top:26px;display:flex;align-items:center;gap:12px}
.brand-mark{width:56px;height:56px;border-radius:50%;background:var(--blue)}
.brand-name{font-size:34px;font-weight:700;color:var(--blue)}
.contact-item{display:flex;align-items:center;gap:10px;font-size:15px;color:var(--blue)}
.contact-item .dot{width:28px;height:28px;border-radius:50%;display:flex;align-items:center;justify-content:center}
.social{display:flex;gap:8px}
.social-icon{width:33px;height:33px;border-radius:50%;border:2px solid #222;display:flex;align-items:center;justify-content:center;color:#222}
.social-icon svg{width:15px;height:15px}
.social-icon.light{border-color:#fff;color:#fff}
.social-icon.lg{width:42px;height:42px}
.social-icon.lg svg{width:19px;height:19px}
.social-icon.md{width:36px;height:36px}
.social-icon.md svg{width:16px;height:16px}

/* nav */
.main-nav{top:114px;height:58px;background:var(--blue)}
.main-nav a{position:absolute;top:0;height:58px;line-height:58px;color:#fff;text-decoration:none;font-size:16px}
.main-nav .active{background:var(--green);left:100px;width:111px;text-align:center}
.search{left:888px;top:10px;width:211px;height:38px;border:2px solid #fff;color:#fff;font-size:15px;padding:8px 12px}

/* hero */
.hero{top:172px;height:518px;
  background:
    linear-gradient(rgba(20,28,40,.35),rgba(20,28,40,.45)),
    radial-gradient(ellipse 260px 200px at 30% 65%,#e9e4dc 0%,rgba(233,228,220,0) 100%),
    radial-gradient(ellipse 300px 180px at 62% 55%,#d8d4cc 0%,rgba(216,212,204,0) 100%),
    radial-gradient(ellipse 220px 260px at 85% 30%,#c4ccd4 0%,rgba(196,204,212,0) 100%),
    radial-gradient(ellipse 200px 220px at 12% 30%,#5e5048 0%,rgba(94,80,72,0) 100%),
    linear-gradient(135deg,#4b5360 0%,#8d949c 45%,#3e4652 100%)}
.hero-title{top:148px;width:100%;text-align:center;color:#fff;font-size:44px;font-weight:700;line-height:64px;letter-spacing:.5px}
.btn-outline{left:530px;top:308px;width:140px;height:52px;border:2px solid #fff;color:#fff;font-size:17px;line-height:48px;text-align:center}

/* features band */
.features{top:690px;height:170px;background:var(--blue)}
.feature-title{color:#fff;font-size:23px;font-weight:700}
.feature-text{color:#e8eef6;font-size:12.5px;line-height:22px;width:320px}

/* welcome */
.welcome{top:860px;height:553px;background:#fff}
.section-title{font-size:30px;font-weight:700;color:var(--blue-dark)}
.section-title em{font-style:normal;color:var(--green)}
.service{width:320px;text-align:center}
.service h3{font-size:20px;font-weight:400;margin-top:30px}
.service p{font-size:13px;line-height:24px;color:var(--muted);margin:14px auto 0;width:270px}
.btn{display:inline-block;width:116px;height:40px;line-height:40px;color:#fff;font-size:14px;font-weight:700;border-radius:3px;margin-top:22px}
.badge{width:150px;height:150px;border-radius:50%;margin:0 auto;display:flex;align-items:center;justify-content:center;border:6px solid #fff;box-shadow:0 0 0 3px currentColor}

/* why */
.why{top:1413px;height:439px;background:linear-gradient(100deg,#0f3f78 0%,#1b5aa1 55%,#1a4f8f 100%)}
.why h2{font-size:29px;font-weight:700;color:#fff}
.why-item h4{font-size:17px;font-weight:700;color:#fff}
.why-item p{font-size:14px;line-height:24px;color:#dbe6f3;margin-top:10px;width:520px}
.app-screens{left:100px;top:46px;width:380px;height:345px;border-radius:14px;
  background:
    radial-gradient(ellipse 90px 140px at 50% 55%,#ffffff 0%,rgba(255,255,255,0) 100%),
    radial-gradient(ellipse 70px 90px at 20% 45%,#a9c8e8 0%,rgba(169,200,232,0) 100%),
    radial-gradient(ellipse 70px 90px at 82% 45%,#c9d9ea 0%,rgba(201,217,234,0) 100%),
    linear-gradient(180deg,#2c6fc0 0%,#2c6fc0 12%,#eef2f7 12%,#e1e8f1 100%)}

/* reports */
.reports{top:1852px;height:403px;background:#fff}
.checklist{list-style:none}
.checklist li{display:flex;align-items:center;gap:14px;height:36px;font-size:14.5px;color:#333}
.tick{width:18px;height:18px;border:2px solid #333;position:relative;flex:none}

/* testimonials */
.testimonials{top:2255px;height:451px;text-align:center;color:#fff;
  background:
    radial-gradient(ellipse 260px 220px at 32% 40%,rgba(200,225,140,.55) 0%,rgba(200,225,140,0) 100%),
    radial-gradient(ellipse 240px 200px at 78% 60%,rgba(90,140,30,.45) 0%,rgba(90,140,30,0) 100%),
    linear-gradient(90deg,#7fb536 0%,#9acb46 45%,#7fb536 100%)}
.testimonials h2{font-size:30px;font-weight:700}
.testimonials p{font-size:14.5px;line-height:26px}

/* footer */
.site-footer{top:2706px;height:335px;
  background:
    radial-gradient(ellipse 300px 200px at 70% 40%,rgba(90,90,90,.5) 0%,rgba(90,90,90,0) 100%),
    linear-gradient(90deg,#1f1f1f,#333 60%,#222)}
.footer-head{font-size:17px;font-weight:700;color:#fff;text-transform:uppercase}
.footer-head::after{content:"";display:block;width:110px;height:1px;background:#888;margin-top:12px}
.links li{list-style:none;color:#fff;font-size:14px;height:32px}
.post{display:flex;gap:18px;height:68px}
.post .thumb{width:60px;height:50px;background:linear-gradient(135deg,#6f7f92,#c9b6a3 60%,#e8e2da)}
.post b{display:block;font-size:14px;color:#fff;font-weight:400}
.post small{display:block;font-size:13px;color:#ddd;margin-top:8px}
.field{width:199px;border:1px solid #aaa;color:#fff;font-size:11px;padding:8px 10px;border-radius:2px}
.bottom-bar{top:3041px;height:62px;background:var(--green)}
</style>
</head>
<body>

<svg width="0" height="0" style="position:absolute">
  <defs>
    <symbol id="i-globe" viewBox="0 0 20 20"><g fill="none" stroke="currentColor" stroke-width="1.8"><circle cx="10" cy="10" r="8"/><ellipse cx="10" cy="10" rx="3.5" ry="8"/><path d="M2 10h16"/></g></symbol>
    <symbol id="i-mail" viewBox="0 0 20 20"><g fill="none" stroke="currentColor" stroke-width="1.8"><rect x="2" y="4" width="16" height="12"/><path d="M2 5l8 6 8-6"/></g></symbol>
    <symbol id="i-share" viewBox="0 0 20 20"><g fill="currentColor"><circle cx="15" cy="4" r="2.6"/><circle cx="5" cy="10" r="2.6"/><circle cx="15" cy="16" r="2.6"/></g><path d="M15 4L5 10l10 6" fill="none" stroke="currentColor" stroke-width="1.6"/></symbol>
    <symbol id="i-chat" viewBox="0 0 20 20"><path d="M2 3h16v11H8l-4 4v-4H2z" fill="none" stroke="currentColor" stroke-width="1.8" stroke-linejoin="round"/></symbol>
    <symbol id="i-link" viewBox="0 0 20 20"><g fill="none" stroke="currentColor" stroke-width="1.8"><rect x="1.5" y="7" width="9" height="6" rx="3"/><rect x="9.5" y="7" width="9" height="6" rx="3"/></g></symbol>
  </defs>
</svg>

<header class="site-header">
  <div class="brand abs">
    <span class="brand-mark"></span>
    <span class="brand-name">RV7</span>
  </div>
  <div class="contact-item abs" style="left:482px;top:40px">
    <span class="dot" style="background:var(--blue)">
      <svg width="14" height="10" viewBox="0 0 14 10"><rect x="0.5" y="0.5" width="13" height="9" fill="none" stroke="#fff"/><path d="M1 1l6 5 6-5" fill="none" stroke="#fff"/></svg>
    </span>
    ops.desk@rv7mail.com
  </div>
  <div class="contact-item abs" style="left:732px;top:40px;color:var(--green)">
    <span class="dot" style="background:var(--green)">
      <svg width="14" height="14" viewBox="0 0 24 24"><path d="M6 2l4 4-2 3c1 3 4 6 7 7l3-2 4 4-3 4C10 21 3 14 2 5z" fill="#fff"/></svg>
    </span>
    555-014-2290
  </div>
  <div class="social abs" style="left:906px;top:37px">
    <span class="social-icon"><svg><use href="#i-globe"/></svg></span>
    <span class="social-icon"><svg><use href="#i-mail"/></svg></span>
    <span class="social-icon"><svg><use href="#i-share"/></svg></span>
    <span class="social-icon"><svg><use href="#i-chat"/></svg></span>
    <span class="social-icon"><svg><use href="#i-link"/></svg></span>
  </div>
</header>

<nav class="main-nav">
  <a class="active" href="#">Home</a>
  <a href="#" style="left:248px">About Us</a>
  <a href="#" style="left:385px">Why RV7</a>
  <a href="#" style="left:526px">Web Application</a>
  <a href="#" style="left:720px">Contact Us</a>
  <div class="search abs">Search
    <svg class="abs" style="right:10px;top:10px" width="14" height="14" viewBox="0 0 14 14"><circle cx="6" cy="6" r="4.5" fill="none" stroke="#fff" stroke-width="2"/><path d="M9.5 9.5L13 13" stroke="#fff" stroke-width="2"/></svg>
  </div>
</nav>

<section class="hero" role="img" aria-label="Photo of a team collaborating around an office table with laptops">
  <h1 class="hero-title abs">EMERGENCY - RAPID VIGIL FIELD<br>OPERATIONS SUITE</h1>
  <div class="btn-outline abs">Read More</div>
  <svg class="abs" style="left:30px;top:255px" width="30" height="54" viewBox="0 0 30 54"><path d="M27 2L3 27l24 25" fill="none" stroke="#fff" stroke-width="2.5"/></svg>
  <svg class="abs" style="left:1134px;top:255px" width="30" height="54" viewBox="0 0 30 54"><path d="M3 2l24 25L3 52" fill="none" stroke="#fff" stroke-width="2.5"/></svg>
</section>

<section class="features">
  <svg class="abs" style="left:0;top:0" width="1200" height="170" viewBox="0 0 1200 170"><polygon points="666,0 1200,0 1200,170 600,170" fill="#8dc63f"/></svg>
  <svg class="abs" style="left:100px;top:36px" width="86" height="86" viewBox="0 0 86 86" fill="none" stroke="#fff" stroke-width="3">
    <circle cx="38" cy="38" r="32"/><ellipse cx="38" cy="38" rx="14" ry="32"/><path d="M6 38h64M12 22h52M12 54h52M38 6v64"/>
    <circle cx="66" cy="66" r="12" fill="#1d5fa8"/><circle cx="66" cy="66" r="4"/>
  </svg>
  <div class="abs" style="left:207px;top:36px">
    <div class="feature-title">WEB APPLICATION</div>
    <p class="feature-text" style="margin-top:10px">The product is focused on Preparing for an incident using Volunteer and Resource management and then responding to an incident.</p>
  </div>
  <svg class="abs" style="left:668px;top:36px" width="80" height="86" viewBox="0 0 80 86" fill="none" stroke="#fff" stroke-width="3">
    <rect x="10" y="8" width="60" height="72" rx="4"/><path d="M22 28l6 6 10-10M22 50l6 6 10-10M46 30h14M46 52h14"/>
  </svg>
  <div class="abs" style="left:793px;top:36px">
    <div class="feature-title">TASKS MANAGEMENT</div>
    <p class="feature-text" style="margin-top:10px">The product is focused on Preparing for an incident using Volunteer and Resource management and then responding to an incident.</p>
  </div>
</section>

<section class="welcome">
  <div class="abs" style="left:574px;top:-26px;width:52px;height:52px;border-radius:50%;background:#fff;border:2px solid var(--blue);color:var(--blue);font-size:15px;font-weight:700;line-height:48px;text-align:center">RV7</div>
  <h2 class="section-title abs" style="top:40px;width:100%;text-align:center">Welcome <em>To RV7</em></h2>
  <p class="abs" style="top:94px;width:100%;text-align:center;font-size:14px">City Officials and Emergency Management Officials can get access to instant statistics</p>

  <div class="service abs" style="left:90px;top:150px">
    <div class="badge" style="background:var(--blue-dark);color:var(--blue-dark)">
      <svg width="70" height="60" viewBox="0 0 70 60" fill="#fff"><circle cx="25" cy="16" r="11"/><circle cx="48" cy="18" r="9"/><path d="M4 54c0-14 10-22 21-22s21 8 21 22z"/><path d="M44 32c12 0 22 8 22 20H50c0-8-3-14-6-20z"/></svg>
    </div>
    <h3 style="color:var(--blue-dark)">Incident Management</h3>
    <p>Easy one click notification to teams on the ground and team members on the same task.</p>
    <span class="btn" style="background:var(--green)">Read More</span>
  </div>

  <div class="service abs" style="left:440px;top:150px">
    <div class="badge" style="background:var(--green);color:var(--green)">
      <svg width="66" height="64" viewBox="0 0 66 64" fill="#fff"><circle cx="33" cy="16" r="12"/><path d="M8 62c0-16 11-26 25-26s25 10 25 26z"/></svg>
    </div>
    <h3 style="color:var(--green-dark)">Volunteer Management</h3>
    <p>Easy one click notification to teams on the ground and team members on the same task.</p>
    <span class="btn" style="background:var(--navy)">Read More</span>
  </div>

  <div class="service abs" style="left:788px;top:150px">
    <div class="badge" style="background:var(--blue-dark);color:var(--blue-dark)">
      <svg width="64" height="64" viewBox="0 0 64 64" fill="none" stroke="#fff" stroke-width="6"><circle cx="26" cy="26" r="18"/><path d="M39 39l20 20" stroke-linecap="round"/></svg>
    </div>
    <h3 style="color:var(--blue-dark)">Damage Assessment</h3>
    <p>Easy one click notification to teams on the ground and team members on the same task.</p>
    <span class="btn" style="background:var(--green)">Read More</span>
  </div>
</section>

<section class="why">
  <div class="app-screens abs" role="img" aria-label="Three smartphones showing the incident map and damage assessment screens"></div>
  <h2 class="abs" style="left:540px;top:40px">Why Adopt RV7</h2>

  <div class="why-item abs" style="left:540px;top:118px">
    <svg class="abs" style="left:0;top:0" width="44" height="40" viewBox="0 0 44 40" fill="none" stroke="#fff" stroke-width="2.5"><rect x="4" y="6" width="28" height="30"/><path d="M10 14h16M10 21h16M10 28h10M32 14h8v22H32"/></svg>
    <div style="margin-left:70px"><h4>HARBOUR DISTRICT</h4><p>The roles from CERT teams have been created to have access to either the web, mobile or both the interfaces.</p></div>
  </div>
  <div class="why-item abs" style="left:540px;top:228px">
    <svg class="abs" style="left:0;top:0" width="44" height="40" viewBox="0 0 44 40" fill="none" stroke="#fff" stroke-width="2.5"><rect x="3" y="3" width="38" height="26"/><path d="M16 36h12M22 29v7"/></svg>
    <div style="margin-left:70px"><h4>FERRY ISLE</h4><p>RV7 offers a web based and mobile interface to assist the CERT</p></div>
  </div>
  <div class="why-item abs" style="left:540px;top:315px">
    <svg class="abs" style="left:0;top:0" width="50" height="44" viewBox="0 0 50 44" fill="#fff"><circle cx="14" cy="14" r="8"/><path d="M0 42c0-12 6-18 14-18s14 6 14 18z"/><rect x="26" y="2" width="22" height="16" rx="2"/></svg>
    <div style="margin-left:70px"><h4>CAPITAL WARD</h4><p>Accurate identification of number of CERT Volunteers available to help in an incident.</p></div>
  </div>
</section>

<section class="reports">
  <div class="abs" style="left:100px;top:40px;display:flex;align-items:center;gap:12px">
    <span style="width:32px;height:32px;border-radius:50%;background:var(--blue);display:block"></span>
    <h2 class="section-title">Reports <em>Console</em></h2>
  </div>
  <ul class="checklist abs" style="left:100px;top:91px">
    <li><span class="tick"><svg class="abs" style="left:1px;top:-6px" width="20" height="18" viewBox="0 0 20 18"><path d="M2 9l5 5L18 2" fill="none" stroke="#333" stroke-width="3"/></svg></span>Easy system to register volunteers.</li>
    <li><span class="tick"><svg class="abs" style="left:1px;top:-6px" width="20" height="18" viewBox="0 0 20 18"><path d="M2 9l5 5L18 2" fill="none" stroke="#333" stroke-width="3"/></svg></span>Accurate identification of number of CERT Volunteers available to help in an incident.</li>
    <li><span class="tick"><svg class="abs" style="left:1px;top:-6px" width="20" height="18" viewBox="0 0 20 18"><path d="M2 9l5 5L18 2" fill="none" stroke="#333" stroke-width="3"/></svg></span>Efficient Communication mechanism to reach out to the volunteers via SMS.</li>
    <li><span class="tick"><svg class="abs" style="left:1px;top:-6px" width="20" height="18" viewBox="0 0 20 18"><path d="M2 9l5 5L18 2" fill="none" stroke="#333" stroke-width="3"/></svg></span>Rich graphical visualization of Incidents &amp; Damages associated with the incidents.</li>
    <li><span class="tick"><svg class="abs" style="left:1px;top:-6px" width="20" height="18" viewBox="0 0 20 18"><path d="M2 9l5 5L18 2" fill="none" stroke="#333" stroke-width="3"/></svg></span>Easy Management and Tracking of resources associated.</li>
    <li><span class="tick"><svg class="abs" style="left:1px;top:-6px" width="20" height="18" viewBox="0 0 20 18"><path d="M2 9l5 5L18 2" fill="none" stroke="#333" stroke-width="3"/></svg></span>Capture Notes and pictures about situations being handled.</li>
    <li><span class="tick"><svg class="abs" style="left:1px;top:-6px" width="20" height="18" viewBox="0 0 20 18"><path d="M2 9l5 5L18 2" fill="none" stroke="#333" stroke-width="3"/></svg></span>Easy one click notification to teams on the ground and team members on the same task.</li>
  </ul>
  <svg class="abs" style="left:765px;top:82px" width="383" height="284" viewBox="0 0 383 284" role="img" aria-label="Bar and pie chart summarising incident reports">
    <line x1="40" y1="250" x2="350" y2="250" stroke="#bbb" stroke-width="2"/>
    <line x1="40" y1="40" x2="40" y2="250" stroke="#bbb" stroke-width="2"/>
    <path d="M40 200h310M40 150h310M40 100h310" stroke="#e6e6e6"/>
    <rect x="70" y="90" width="30" height="160" fill="#8dc63f"/>
    <rect x="112" y="40" width="30" height="210" fill="#5a3fa0"/>
    <rect x="154" y="70" width="30" height="180" fill="#e53e8c"/>
    <rect x="196" y="110" width="30" height="140" fill="#f2c230"/>
    <rect x="238" y="60" width="30" height="190" fill="#1d5fa8"/>
    <circle cx="318" cy="120" r="34" fill="#1d5fa8"/>
    <path d="M318 120V86a34 34 0 0 1 32 46z" fill="#8dc63f"/>
    <path d="M318 120l32 12a34 34 0 0 1-28 22z" fill="#f2c230"/>
  </svg>
</section>

<section class="testimonials" role="img" aria-label="Green tinted photo of a smiling team member behind the testimonial">
  <div class="abs" style="left:556px;top:30px;width:88px;height:88px;border-radius:50%;border:3px solid #fff;font-size:26px;font-weight:700;line-height:82px">RV7</div>
  <h2 class="abs" style="top:155px;width:100%">Team Testimonials</h2>
  <svg class="abs" style="left:158px;top:222px" width="26" height="20" viewBox="0 0 26 20" fill="#fff"><path d="M0 20V10L6 0h5L7 10h4v10zM15 20V10l6-10h5l-4 10h4v10z"/></svg>
  <p class="abs" style="left:210px;top:250px;width:780px">Lorem ipsum dolor sit amet consectetur labore magna aliqua elit sed do eiusmod tempor incididunt ut labore et dolore magna aliqua veranesa at denim voluptatem accusantium doloremque laudantium, totam rem aperiam, eaque ipsa consec labore et dolore magna aliqua.</p>
  <svg class="abs" style="left:1022px;top:305px" width="26" height="20" viewBox="0 0 26 20" fill="#fff"><path d="M26 0v10l-6 10h-5l4-10h-4V0zM11 0v10L5 20H0l4-10H0V0z"/></svg>
  <div class="abs" style="top:362px;left:0;width:100%;display:flex;justify-content:center;gap:10px">
    <span class="social-icon light lg"><svg><use href="#i-globe"/></svg></span>
    <span class="social-icon light lg"><svg><use href="#i-mail"/></svg></span>
    <span class="social-icon light lg"><svg><use href="#i-share"/></svg></span>
    <span class="social-icon light lg"><svg><use href="#i-chat"/></svg></span>
    <span class="social-icon light lg"><svg><use href="#i-link"/></svg></span>
  </div>
</section>

<footer class="site-footer" role="img" aria-label="Dark tinted office photo behind the footer">
  <div class="abs" style="left:155px;top:70px;width:120px;height:120px;border-radius:50%;border:3px solid #fff;color:#fff;font-size:34px;font-weight:700;line-height:114px;text-align:center">RV7</div>
  <div class="abs" style="left:60px;top:205px;width:310px;text-align:center;color:#fff;font-size:20px;font-weight:700;line-height:35px">Rapid Vigil Field<br>Operations Suite</div>

  <div class="abs" style="left:391px;top:50px">
    <div class="footer-head">Quick Links</div>
    <ul class="links" style="margin-top:24px">
      <li>› Home</li><li>› About Us</li><li>› Why RV7</li><li>› Web Application</li><li>› Blog</li><li>› Contact Us</li>
    </ul>
  </div>

  <div class="abs" style="left:583px;top:50px">
    <div class="footer-head">Recent Posts</div>
    <div style="margin-top:24px">
      <div class="post"><div class="thumb" role="img" aria-label="Post thumbnail photo"></div><div><b>Resource management</b><small>▦ NOV 12, 2015</small></div></div>
      <div class="post"><div class="thumb" role="img" aria-label="Post thumbnail photo"></div><div><b>Incident Management</b><small>▦ NOV 12, 2015</small></div></div>
      <div class="post"><div class="thumb" role="img" aria-label="Post thumbnail photo"></div><div><b>Team Management</b><small>▦ NOV 12, 2015</small></div></div>
    </div>
  </div>

  <div class="abs" style="left:900px;top:50px">
    <div class="footer-head">Contact Form</div>
    <div class="field abs" style="top:50px;height:35px">Name</div>
    <div class="field abs" style="top:93px;height:35px">Phone</div>
    <div class="field abs" style="top:136px;height:63px">Message</div>
    <div class="abs" style="top:217px;width:120px;height:35px;background:var(--green);color:#fff;font-size:11px;line-height:35px;text-align:center">SEND MESSAGE</div>
  </div>
</footer>

<section class="bottom-bar">
  <p class="abs" style="left:100px;top:23px;color:#fff;font-size:12px">Copyright © 2016 RV7. All Right Reserved</p>
  <div class="abs" style="left:910px;top:12px;display:flex;gap:6px">
    <span class="social-icon light md"><svg><use href="#i-globe"/></svg></span>
    <span class="social-icon light md"><svg><use href="#i-mail"/></svg></span>
    <span class="social-icon light md"><svg><use href="#i-share"/></svg></span>
    <span class="social-icon light md"><svg><use href="#i-chat"/></svg></span>
    <span class="social-icon light md"><svg><use href="#i-link"/></svg></span>
  </div>
</section>

</body>
</html>
```